Venture Capital Investment Firm

We are looking to overhaul our existing website (substantially), with only using the same logos (which we can provide).
We are an investment firm that focuses on making loans to late stage technology companies. Our site should ultimately look like other venture capital firms, and look modern and fresh. We have an existing website www.norvellhub.com which this will be replacing, although we will be using a lot of the existing written content, and potentially the numbers of pages we will need, we are not wed to anything else. Please feel free to shoot any questions at any time and thank you in advance for your help!
Websites we like as examples:
https://www.tesmarkfund.com/
https://www.brindlewoodpartners.com/
Target Market(s)
Potential investors who will invest in our firm, as well as potentially companies that are looking to borrow money from us.
Coding
Coded - Design and coding required
Number of Pages Required
5+ page
Colors
Designer to choose colors to be used in the design.
Look and feel

```html
<!DOCTYPE html>
<html lang="en">
<head>
<meta charset="utf-8">
<title>Norvell Hub — Team</title>
<link href="https://fonts.googleapis.com/css2?family=Raleway:wght@300;400;500;700&display=swap" rel="stylesheet">
<style>
:root{
  --navy:#0d1d4a;
  --ink:#2a2f45;
  --body:#6a6f80;
  --accent:#2f8fb8;
  --panel:#f6f7f9;
  --line:#4d9cc0;
  --sq-light:#5bb8e0;
  --sq-dark:#1b7fc4;
  --footer:#1f4252;
  --white:#ffffff;
}
*{margin:0;padding:0;box-sizing:border-box}
html,body{width:1200px;height:3054px;overflow:hidden}
body{position:relative;background:var(--white);font-family:"Raleway",sans-serif;color:var(--ink)}
.hero{position:absolute;left:0;top:0;width:1200px;height:548px;
  background:linear-gradient(180deg,#5d9bb9 0%,#a9c7d6 30%,#dfe6ec 55%,#ecdde0 70%,#c9b8b8 76%,#6c5a56 82%,#3b3a42 90%,#2c3442 100%)}
.logo{position:absolute;left:149px;top:22px;display:flex;align-items:center;gap:12px}
.logo-mark{width:34px;height:34px;border-radius:50%;background:var(--navy)}
.logo-name{font-weight:500;font-size:24px;color:var(--navy);letter-spacing:.5px}
.nav{position:absolute;top:37px;left:0;width:1200px}
.nav a{position:absolute;font-size:11px;color:#34466a;text-decoration:none;letter-spacing:.3px;text-transform:uppercase}
.nav a.active{text-decoration:underline}
.login{position:absolute;left:906px;top:21px;width:144px;height:42px;border:1.5px solid var(--navy);border-radius:21px;
  font-size:11px;color:var(--navy);display:flex;align-items:center;justify-content:center;letter-spacing:.3px}
.hero-title{position:absolute;top:212px;width:1200px;text-align:center;font-size:45px;font-weight:400;color:var(--navy)}
.hero-sub{position:absolute;top:275px;width:1200px;text-align:center;font-size:16px;font-weight:400;color:var(--ink)}
.divider{position:absolute;left:600px;top:510px;width:1px;height:78px;background:var(--line)}
.photo{position:absolute;left:149px;width:333px;height:366px;background:radial-gradient(ellipse at 50% 45%,#6a6a6a 0%,#2a2a2a 45%,#0c0c0c 100%)}
.panel{position:absolute;left:457px;width:593px;background:var(--panel);padding:38px 38px 0 66px}
.head{display:flex;justify-content:space-between;align-items:flex-start}
.name{font-size:16px;color:var(--navy);font-weight:400}
.name b{font-weight:700}
.role{font-size:11px;letter-spacing:2px;color:var(--accent);text-transform:uppercase;margin-top:5px}
.social{display:flex;gap:12px}
.social span{width:32px;height:32px;border-radius:5px;display:block}
.social .s1{background:var(--sq-light)}
.social .s2{background:var(--sq-dark)}
.bio{margin-top:30px;width:465px}
.bio p{font-size:11.5px;line-height:19.5px;color:var(--body);font-weight:400;margin-bottom:12px}
.cta{position:absolute;left:522px;top:2479px;width:156px;height:44px;border:1.5px solid var(--navy);border-radius:22px;
  display:flex;align-items:center;justify-content:center;font-size:13px;color:var(--navy)}
.footer{position:absolute;left:0;top:2710px;width:1200px;height:344px;background:linear-gradient(180deg,#1d3f51 0%,#24485a 60%,#2e5364 100%)}
.f-logo{position:absolute;top:2810px;width:1200px;display:flex;justify-content:center;align-items:center;gap:14px}
.f-logo .logo-mark{background:var(--white);width:44px;height:44px}
.f-logo .logo-name{color:var(--white);font-size:38px}
.f-nav a{position:absolute;top:2916px;font-size:11px;color:var(--white);letter-spacing:.3px;text-decoration:none}
.f-meta{position:absolute;width:1200px;text-align:center;color:var(--white);font-size:7px}
.f-meta u{text-decoration:underline}
</style>
</head>
<body>

<div class="hero" role="img" aria-label="Aerial photo of a city skyline at dawn under a pale blue sky"></div>
<div class="logo"><span class="logo-mark"></span><span class="logo-name">Norvell Hub</span></div>
<nav class="nav">
  <a style="left:398px">Strategy</a>
  <a style="left:510px">About Us</a>
  <a class="active" style="left:622px">Team</a>
  <a style="left:708px">News</a>
  <a style="left:798px">Contact</a>
</nav>
<div class="login">INVESTORS LOGIN</div>
<h1 class="hero-title">Meet Our Experts</h1>
<p class="hero-sub">The Senoir Team of Norvell Hub</p>
<div class="divider"></div>

<div class="photo" style="top:642px" role="img" aria-label="Black and white portrait of Marcus Ellery"></div>
<section class="panel" style="top:699px;height:480px">
  <div class="head">
    <div><div class="name"><b>Marcus Ellery</b>, Managing Partner</div><div class="role">Life Sciences, Technology</div></div>
    <div class="social"><span class="s1"></span><span class="s2"></span></div>
  </div>
  <div class="bio">
    <p>Marcus Ellery is an industry leader with over $1.2B in structured credit investments since 2004. Marcus focuses on origination, underwriting, and portfolio management across sectors at Norvell Hub.</p>
    <p>Mr. Ellery was the co-founder of Brightwell Health Partners, a life sciences focused structured credit fund, from 2010-2014. From 2004-2010, Mr. Ellery was Managing Director and Co-Head of the Healthcare Group for the Keystone Bridge Special Opportunities Fund at Rampart Investment Group.</p>
    <p>Prior to joining Rampart, Mr. Ellery was a member of the investment team at Halvern Capital where he executed mezzanine debt and leveraged buyouts for middle market companies. Previously, he worked in the Leveraged Finance Group of Tollard Brothers, where he structured and underwrote bank loan, high yield bond, and mezzanine debt transactions. Mr. Ellery began his career with Corvane Capital's Merchant Banking Group. Mr. Ellery earned his joint JD/MBA degrees from Lakemont Reserve University and a BS in Finance from Ridgeway State University.</p>
  </div>
</section>

<div class="photo" style="top:1255px" role="img" aria-label="Black and white portrait of Devan Rasheed"></div>
<section class="panel" style="top:1313px;height:460px">
  <div class="head">
    <div><div class="name"><b>Devan Rasheed</b>, Managing Partner</div><div class="role">Technology</div></div>
    <div class="social"><span class="s1"></span><span class="s2"></span></div>
  </div>
  <div class="bio">
    <p>Devan Rasheed leads technology investment origination and evaluation at Norvell Hub. He has over 15 years of technology investment and transaction experience.</p>
    <p>Mr. Rasheed was a Managing Director and Head of the Aldenberg Bank Technology Mergers &amp; Acquisitions practice in San Francisco from 2011-2013. Prior to joining Aldenberg Bank in 2011, Mr. Rasheed was a Managing Director with Whitcombe &amp; Co's Technology Banking practice in San Francisco and focused on the Semiconductors and Hardware coverage effort. Previously, Mr. Rasheed spent over 7 years with Ostrander Group's Technology M&amp;A Group in Palo Alto and served as a co-head of the Semiconductor Banking Practice.</p>
    <p>As an investment banker, Devan worked globally with large technology firms, emerging companies, venture capitalists, and technology private equity firms, advising on transactions totaling in excess of $75B. Mr. Rasheed received an MBA from the University of Eastbrook Graduate School of Business, MSc from the Thameside School of Economics, and a BA from Crestfield University.</p>
  </div>
</section>

<div class="photo" style="top:1849px" role="img" aria-label="Black and white portrait of Owen Fairley"></div>
<section class="panel" style="top:1907px;height:479px">
  <div class="head">
    <div><div class="name"><b>Owen Fairley</b>, Partner</div><div class="role">Chief Operating Officer</div></div>
    <div class="social"><span class="s1"></span><span class="s2"></span></div>
  </div>
  <div class="bio">
    <p>Owen Fairley serves as the Chief Operating Officer at Norvell Hub. He has 20 years of experience in the alternative-investment markets, including private equity fund and firm formation, operations, capital-raising, investor relations, portfolio management and legal transactions.</p>
    <p>Before joining Norvell Hub, Mr. Fairley served as a Managing Director at Silverbrook &amp; Co. and as a Partner at Interlace Capital in San Francisco. From 2004 to 2013, he worked as a principal and Managing Director at Veritan Partners, where he led private fund placements totaling over $15 billion. Previously, Mr. Fairley co-managed a group of technology and life-science-focused funds of funds as part of Ostrander Group private equity. He also worked as a corporate finance attorney at Hartwell LLP and Pemberton Cole LLP, where he represented emerging growth technology companies and investors. Prior to attending law school, he served as Assistant Press Secretary to US Senator Thomas Albright Keane of New York.</p>
    <p>Mr. Fairley received a BA from Harrow University and a JD from the University of Eastbrook.</p>
  </div>
</section>

<div class="cta">Read Our News</div>

<footer>
  <div class="footer" role="img" aria-label="Dimmed photo of a suspension bridge over the bay"></div>
  <div class="f-logo"><span class="logo-mark"></span><span class="logo-name">Norvell Hub</span></div>
  <nav class="f-nav">
    <a style="left:362px">STRATEGY</a>
    <a style="left:479px">ABOUT US</a>
    <a style="left:597px">TEAM</a>
    <a style="left:688px">NEWS</a>
    <a style="left:782px">CONTACT</a>
  </nav>
  <p class="f-meta" style="top:3019px">Norvell Hub &nbsp;•&nbsp; San Francisco</p>
  <p class="f-meta" style="top:3032px">© 2020 Norvell Hub Investment Partners LLC. All Rights Reserved. &nbsp;|&nbsp; <u>Legal Disclaimer</u></p>
</footer>

</body>
</html>
```